I want a website to be designed for our new company, it's an import and export company for variety of things.

please see the attached Logo for our company and the Images for our different sections for our busienss

Target Market(s)

multiple

Coding

Coded - Design and coding required

Number of Pages Required

5+ page

Font styles to use
Sans Serif

Colors

Designer to choose colors to be used in the design.

Requirements
Must have
• KVR GLOBALINKS
• KVR globalinks Trading & Contracting provides various services. The Company offers infrastructure construction, oil, enegy and gas services, agricultural projects, real estate development, travel and tourism, and food processing and trading.
• Civil contracting for infrastructure, residential and heavy projects. Through its main subsidiaries; distribution of general food products, construction chemicals including corrosion inhibitors and electrical machinery; provides catering and travel agency services; ownership and operation of a school; offers human sources services including manpower supply.
• Drilling and Gold Mines Used Machinery, All Kinds of Construction Machinery, Drilling Machines are manufactured and sold.
Nice to have
• good designa and beautiful colours, it has too look professional

```html
<!DOCTYPE html>
<html lang="en">
<head>
<meta charset="utf-8">
<title>KVR GLOBALINKS</title>
<link href="https://fonts.googleapis.com/css2?family=Cinzel:wght@400;600;700&family=Mulish:wght@400;600;700;800&display=swap" rel="stylesheet">
<style>
:root{
  --red:#8e1b22;
  --red-bright:#a41e26;
  --ink:#111111;
  --black:#141414;
  --text:#2b2b2b;
  --muted:#555;
  --white:#ffffff;
  --panel:#d9d9d9;
  --field:#efefef;
  --rule:#cfcfcf;
}
*{box-sizing:border-box;margin:0;padding:0}
html,body{width:1200px;height:3569px;overflow:hidden}
body{position:relative;background:var(--white);font-family:'Mulish',sans-serif;color:var(--text)}
.abs{position:absolute}
.serif{font-family:'Cinzel',serif}

/* nav */
.topnav{left:0;top:0;width:1200px;height:58px;background:var(--ink)}
.topnav a{position:absolute;top:0;height:58px;line-height:62px;color:#fff;font-size:14px;text-decoration:none;letter-spacing:.5px}
.topnav .active{left:76px;width:136px;background:var(--red);text-align:center;font-weight:800;font-size:13px;letter-spacing:1px}
.header{left:0;top:58px;width:1200px;height:111px;background:var(--black)}
.header .call{left:76px;top:44px;color:#fff;font-size:24px;font-weight:700}
.header .mail{right:75px;top:48px;color:#fff;font-size:20px;font-weight:700}
.logo-cap{left:444px;top:130px;width:312px;height:88px;background:var(--black);border-radius:0 0 156px 156px/0 0 88px 88px;z-index:3}
.brand{left:444px;top:126px;width:312px;text-align:center;color:#fff;font-family:'Cinzel',serif;font-size:18px;letter-spacing:2px;z-index:4}

/* hero */
.hero{left:0;top:169px;width:1200px;height:697px}
.hero-title{left:578px;top:365px;color:var(--red);font-family:'Cinzel',serif;font-size:45px;font-weight:700;letter-spacing:1px}
.hero-sub{left:578px;top:430px;width:520px;color:var(--red);font-size:23px;font-weight:600;line-height:29px}
.btn-dark{left:578px;top:517px;width:165px;height:41px;background:var(--ink);color:#fff;font-family:'Cinzel',serif;font-size:18px;text-align:center;line-height:41px}

/* section heads */
.mark{left:570px;width:60px;height:60px;border:3px solid var(--text);border-radius:50%}
.h2{left:0;width:1200px;text-align:center;font-family:'Cinzel',serif;color:var(--ink);font-weight:600;letter-spacing:1px}
.lead{left:180px;width:840px;text-align:center;font-size:17px;line-height:28px;color:#333}
.btn-outline{height:42px;border:2px solid var(--red);color:var(--ink);font-family:'Cinzel',serif;font-size:18px;text-align:center;line-height:38px}
.rule{left:75px;width:1052px;height:5px;border-top:1px solid var(--rule);border-bottom:1px solid var(--rule)}

/* services */
.tabs{left:0;width:1200px;top:1398px;text-align:center;font-family:'Cinzel',serif;font-size:22px;color:var(--ink)}
.tab-on{color:var(--red);border-bottom:2px solid var(--red);padding-bottom:3px}
.card{width:329px;height:181px;box-shadow:0 3px 8px rgba(0,0,0,.35);overflow:hidden}
.card .label{position:absolute;left:0;bottom:16px;height:24px;line-height:24px;padding:0 50px 0 22px;background:var(--red);color:#fff;font-size:16px;font-weight:700;clip-path:polygon(0 0,100% 0,88% 100%,0 100%)}
.card .over{position:absolute;left:28px;top:20px;width:270px;color:#fff;font-family:Arial,sans-serif;font-size:13px;line-height:22px}

/* blog */
.blog{left:0;top:1974px;width:1200px;height:537px;background:linear-gradient(180deg,#2a2a2a 0%,#3a3836 45%,#4a4440 75%,#2b2a29 100%)}
.blog-text{left:195px;top:2168px;width:840px;text-align:center;color:#eee;font-size:16.5px;line-height:28px}
.arrow{top:2200px;width:30px;height:34px}
.meta{left:381px;top:2331px;width:446px;height:39px;background:var(--red-bright);color:#fff;font-size:16px;line-height:39px;text-align:center;clip-path:polygon(4% 0,100% 0,96% 100%,0 100%)}

/* contact */
.form{left:145px;top:2720px;width:911px;height:322px;background:var(--panel);box-shadow:0 3px 8px rgba(0,0,0,.25)}
.field{background:var(--field);font-size:11px;font-weight:700;color:#333;padding:10px 16px}

/* footer */
.foot-h{top:3222px;color:#fff;font-size:23px;font-weight:800}
.foot-list{top:3271px;color:#fff;font-size:15px;list-style:none}
.foot-list li{height:33px;display:flex;align-items:flex-start;gap:14px}
.foot-list svg{flex:none;margin-top:3px}
.social{top:3280px;width:26px;height:26px;border-radius:50%;background:#fff}
.copy{left:0;top:3520px;width:1200px;height:49px;background:#d6d6d6;text-align:center;line-height:49px;font-size:14px;font-weight:700;color:#111}
</style>
</head>
<body>

<nav class="abs topnav">
  <a class="active" href="#">HOME</a>
  <a href="#" style="left:259px">About Us</a>
  <a href="#" style="left:421px">Services</a>
  <a href="#" style="left:575px">Customers</a>
  <a href="#" style="left:740px">Blog</a>
  <a href="#" style="left:838px">Contact Us</a>
  <svg class="abs" style="left:1063px;top:24px" width="16" height="16" viewBox="0 0 16 16"><circle cx="6.5" cy="6.5" r="4.5" fill="none" stroke="#fff" stroke-width="2"/><line x1="10" y1="10" x2="14" y2="14" stroke="#fff" stroke-width="2"/></svg>
  <svg class="abs" style="left:1102px;top:25px" width="18" height="14" viewBox="0 0 18 14"><rect y="1" width="18" height="2" fill="#fff"/><rect y="6" width="18" height="2" fill="#fff"/><rect y="11" width="18" height="2" fill="#fff"/></svg>
</nav>

<header class="abs header">
  <div class="abs call"><svg width="22" height="22" viewBox="0 0 24 24" style="vertical-align:-3px"><path fill="#fff" d="M6.6 10.8c1.4 2.8 3.8 5.1 6.6 6.6l2.2-2.2c.3-.3.7-.4 1-.2 1.1.4 2.3.6 3.6.6.6 0 1 .4 1 1V20c0 .6-.4 1-1 1C10.6 21 3 13.4 3 4c0-.6.4-1 1-1h3.5c.6 0 1 .4 1 1 0 1.3.2 2.5.6 3.6.1.3 0 .7-.2 1z"/></svg> Call Us :&nbsp; 1-800 555 0142</div>
  <div class="abs mail"><svg width="18" height="14" viewBox="0 0 18 14" style="vertical-align:0"><rect x="1" y="1" width="16" height="12" fill="none" stroke="#fff" stroke-width="2"/><path d="M1 1l8 7 8-7" fill="none" stroke="#fff" stroke-width="2"/></svg> info@kvrglobalinks.com</div>
</header>
<div class="abs logo-cap"></div>
<div class="abs brand">KVR GLOBALINKS</div>

<svg class="abs hero" width="1200" height="697" viewBox="0 0 1200 697" role="img" aria-label="Engineer in hard hat and safety vest holding a tablet at a construction site with cranes and trucks">
  <defs>
    <linearGradient id="heroSky" x1="0" y1="0" x2="0" y2="1">
      <stop offset="0" stop-color="#f4f5f7"/>
      <stop offset=".45" stop-color="#d9dde1"/>
      <stop offset=".7" stop-color="#9e8e86"/>
      <stop offset="1" stop-color="#4b4544"/>
    </linearGradient>
    <linearGradient id="heroWorker" x1="0" y1="0" x2="0" y2="1">
      <stop offset="0" stop-color="#e6e2dc"/>
      <stop offset=".45" stop-color="#e46a2a"/>
      <stop offset="1" stop-color="#2b3347"/>
    </linearGradient>
  </defs>
  <path d="M0 0H1200V586Q600 800 0 586Z" fill="url(#heroSky)"/>
  <path d="M200 120H540V690Q370 700 200 660Z" fill="url(#heroWorker)" opacity=".55"/>
</svg>
<div class="abs hero-title">KVR GLOBALINKS</div>
<div class="abs hero-sub">We are an import and export company for a variety of things.</div>
<div class="abs btn-dark">Read More</div>

<!-- welcome -->
<div class="abs mark" style="top:899px"></div>
<h1 class="abs h2" style="top:966px;font-size:44px">WELCOME TO KVR GLOBALINKS</h1>
<p class="abs lead" style="top:1031px">KVR globalinks Trading &amp; Contracting provides various services. The Company offers infrastructure construction, oil, enegy and gas services, agricultural projects, real estate development, travel and tourism, and food processing and trading.</p>
<div class="abs btn-outline" style="left:518px;top:1132px;width:164px">Read More</div>
<div class="abs rule" style="top:1223px"></div>

<!-- services -->
<div class="abs mark" style="top:1248px"></div>
<h2 class="abs h2" style="top:1307px;font-size:44px">OUR SERVICES</h2>
<p class="abs" style="left:0;width:1200px;top:1367px;text-align:center;font-size:14px;color:#333">Lorem ipsum dolor sit amet tellus</p>
<div class="abs tabs"><span class="tab-on">TRADING</span>&nbsp;&nbsp;&nbsp;&nbsp;|&nbsp;&nbsp;&nbsp;&nbsp;CONTRACTING</div>
<svg class="abs" style="left:485px;top:1431px" width="14" height="8" viewBox="0 0 14 8"><path d="M0 0h14L7 8z" fill="var(--red)"/></svg>

<div class="abs card" style="left:75px;top:1487px;background:linear-gradient(135deg,#f6f4ef 0%,#d9a35a 45%,#b6352b 75%,#f3efe9 100%)" role="img" aria-label="Assorted groceries, vegetables and bottled food products"><span class="label">Food products</span></div>
<div class="abs card" style="left:436px;top:1487px;background:linear-gradient(160deg,#3a302c 0%,#1e1a19 60%,#2d2624 100%)" role="img" aria-label="Dark industrial site silhouette"><p class="over">Sed ut perspiciatis unde omnis iste natus error sit voluptatem accusantium doloremque laudantium, totam rem aperiam, eaque ipsa quae ab illo inventore</p><span class="label">Construction chemicals</span></div>
<div class="abs card" style="left:798px;top:1487px;background:linear-gradient(135deg,#6f625a 0%,#b58a5d 45%,#3a2c25 100%)" role="img" aria-label="Grinding machine throwing sparks"><span class="label">Electrical machinery</span></div>

<div class="abs card" style="left:75px;top:1703px;background:linear-gradient(160deg,#4c5b5d 0%,#2f4548 55%,#1d2b2e 100%)" role="img" aria-label="Offshore oil rig at sea seen from above"><span class="label">Oil</span></div>
<div class="abs card" style="left:436px;top:1703px;background:linear-gradient(180deg,#9fb6bd 0%,#d6d2c4 50%,#9b7a52 100%)" role="img" aria-label="Wind turbines on a hillside"><span class="label">Enegy</span></div>
<div class="abs card" style="left:798px;top:1703px;background:linear-gradient(180deg,#2f5aa8 0%,#7d8fb0 45%,#e7a23c 80%,#3a2a1a 100%)" role="img" aria-label="Oil pump jack silhouetted at sunset"><span class="label">Gas</span></div>

<div class="abs rule" style="top:1945px"></div>

<!-- blog -->
<div class="abs blog" role="img" aria-label="Oil pump jacks silhouetted at dusk"></div>
<div class="abs mark" style="left:573px;top:2023px;width:54px;height:54px;border-color:#fff"></div>
<h2 class="abs h2" style="top:2077px;font-size:42px;color:#fff">BLOG</h2>
<p class="abs blog-text">Sed ut perspiciatis unde omnis iste natus error sit voluptatem accusantium doloremque laudantium, totam rem aperiam, eaque ipsa quae ab illo inventore veritatis et quasi architecto beatae vitae dicta sunt explicabo. Nemo enim ipsam voluptatem quia voluptas sit aspernatur aut odit aut fugit, sed quia consequuntur magni dolores eos qui ratione voluptatem sequi nesciunt. Neque porro quisquam est, qui dolorem ipsum quia dolor sit amet, consectetur,</p>
<svg class="abs arrow" style="left:107px" viewBox="0 0 30 34"><path d="M20 6L9 17l11 11" fill="none" stroke="#fff" stroke-width="5"/></svg>
<svg class="abs arrow" style="left:1063px" viewBox="0 0 30 34"><path d="M10 6l11 11-11 11" fill="none" stroke="#fff" stroke-width="5"/></svg>
<div class="abs meta">
  <svg width="15" height="15" viewBox="0 0 16 16" style="vertical-align:-2px"><circle cx="8" cy="5" r="3.5" fill="none" stroke="#fff" stroke-width="1.5"/><path d="M1.5 15c0-4 3-6 6.5-6s6.5 2 6.5 6z" fill="none" stroke="#fff" stroke-width="1.5"/></svg>
  By : Mara Ellison &nbsp;&nbsp;
  <svg width="15" height="15" viewBox="0 0 16 16" style="vertical-align:-2px"><rect x="1.5" y="3" width="13" height="11.5" fill="none" stroke="#fff" stroke-width="1.5"/><line x1="1.5" y1="6.5" x2="14.5" y2="6.5" stroke="#fff" stroke-width="1.5"/><line x1="5" y1="1" x2="5" y2="4" stroke="#fff" stroke-width="1.5"/><line x1="11" y1="1" x2="11" y2="4" stroke="#fff" stroke-width="1.5"/></svg>
  Date : 12-01-2020
</div>

<div class="abs rule" style="top:2529px"></div>

<!-- contact -->
<div class="abs mark" style="top:2557px"></div>
<h2 class="abs h2" style="top:2614px;font-size:44px">CONTACT US</h2>
<p class="abs" style="left:0;width:1200px;top:2673px;text-align:center;font-size:17px;font-weight:700;color:#222">to contact us please use the form below</p>
<form class="abs form">
  <div class="abs field" style="left:61px;top:39px;width:383px;height:34px">Name*</div>
  <div class="abs field" style="left:465px;top:39px;width:384px;height:34px">Email*</div>
  <div class="abs field" style="left:61px;top:95px;width:788px;height:102px">How May We Help You?</div>
  <div class="abs btn-outline" style="left:373px;top:236px;width:164px;height:41px;font-size:15px;line-height:37px">Submit</div>
</form>

<!-- footer -->
<svg class="abs" style="left:0;top:3104px" width="1200" height="416" viewBox="0 0 1200 416"><path d="M0 60Q600 -55 1200 60V416H0Z" fill="var(--black)"/></svg>

<div class="abs foot-h" style="left:79px">Quick Links</div>
<ul class="abs foot-list" style="left:82px">
  <li><svg width="8" height="12" viewBox="0 0 8 12"><path d="M1 1l5 5-5 5" fill="none" stroke="#fff" stroke-width="2"/></svg><span style="margin-left:10px">Home</span></li>
  <li><svg width="8" height="12" viewBox="0 0 8 12"><path d="M1 1l5 5-5 5" fill="none" stroke="#fff" stroke-width="2"/></svg><span style="margin-left:10px">About Us</span></li>
  <li><svg width="8" height="12" viewBox="0 0 8 12"><path d="M1 1l5 5-5 5" fill="none" stroke="#fff" stroke-width="2"/></svg><span style="margin-left:10px">Services</span></li>
  <li><svg width="8" height="12" viewBox="0 0 8 12"><path d="M1 1l5 5-5 5" fill="none" stroke="#fff" stroke-width="2"/></svg><span style="margin-left:10px">Blog</span></li>
  <li><svg width="8" height="12" viewBox="0 0 8 12"><path d="M1 1l5 5-5 5" fill="none" stroke="#fff" stroke-width="2"/></svg><span style="margin-left:10px">Contact Us</span></li>
</ul>

<div class="abs foot-h" style="left:366px">Address</div>
<ul class="abs foot-list" style="left:364px">
  <li><svg width="12" height="16" viewBox="0 0 12 16"><path d="M6 0a6 6 0 0 0-6 6c0 4.5 6 10 6 10s6-5.5 6-10a6 6 0 0 0-6-6z" fill="#fff"/><circle cx="6" cy="6" r="2.2" fill="var(--black)"/></svg><span style="margin-left:8px">#123 Lorium ipsum</span></li>
  <li><span style="margin-left:34px">dolor amit,</span></li>
  <li><span style="margin-left:34px">NZ : 1004</span></li>
</ul>

<div class="abs foot-h" style="left:647px">Contacts</div>
<ul class="abs foot-list" style="left:648px">
  <li><svg width="16" height="12" viewBox="0 0 16 12"><rect width="16" height="12" fill="#fff"/><path d="M0 0l8 6 8-6" fill="none" stroke="var(--black)" stroke-width="1.5"/></svg><span style="margin-left:12px">contact@kvrglobalinks.com</span></li>
  <li><svg width="16" height="16" viewBox="0 0 24 24"><path fill="#fff" d="M6.6 10.8c1.4 2.8 3.8 5.1 6.6 6.6l2.2-2.2c.3-.3.7-.4 1-.2 1.1.4 2.3.6 3.6.6.6 0 1 .4 1 1V20c0 .6-.4 1-1 1C10.6 21 3 13.4 3 4c0-.6.4-1 1-1h3.5c.6 0 1 .4 1 1 0 1.3.2 2.5.6 3.6.1.3 0 .7-.2 1z"/></svg><span style="margin-left:12px">1-800 555 0176</span></li>
  <li><svg width="16" height="16" viewBox="0 0 16 16"><rect x="1" y="5" width="14" height="10" fill="#fff"/><rect x="4" y="1" width="8" height="5" fill="none" stroke="#fff" stroke-width="1.5"/><rect x="4" y="8" width="8" height="4" fill="var(--black)"/></svg><span style="margin-left:12px">1-800 555 0193</span></li>
</ul>

<div class="abs foot-h" style="left:972px">Follow Us</div>
<div class="abs social" style="left:971px"></div>
<div class="abs social" style="left:1028px"></div>
<div class="abs social" style="left:1084px"></div>
<div class="abs" style="left:921px;top:3388px;width:196px;text-align:center;color:#fff;font-family:'Cinzel',serif;font-size:16px;letter-spacing:2px">KVR GLOBALINKS</div>

<div class="abs copy">copyright 2020 &nbsp;|&nbsp; www.kvrglobalinks.com</div>

</body>
</html>
```